Etiketten-Design für nachhaltige Rasur- & Pflegeprodukte
> Wir suchen Verpackung und Etiketten für eine Marke für nachhaltige Rasur- & Pflegeprodukte.
Habedere liebe Designer,
„Habedere“ sagt man bei uns in Bayern, es bedeutet Hallo oder auf Wiedersehen, je nach Gelegenheit. In diesem Fall: Hallo.
Vielleicht kennst du uns schon, wir sind greenpines, wir betreiben einen kleinen Shop für Bartpflege & Rasur unter greenpines-shop.de und wir versuchen uns nun an einem neuen Thema: nachhaltige Rasur- & Pflegeprodukte für Frauen.
Das machen wir unter dem Namen „Sanft“.
Weil die Frage schon oft aufkam: Jawohl, wir haben uns dafür die Beine und die Achseln mit einem Rasierhobel rasiert.
> Zielgruppe.
Wir arbeiten an einer neuen Pflegelinie für Frauen, die sich vorwiegend mit der Rasur und den dazugehörigen Pflegeprodukten beschäftigt. Die Zielgruppe sind vor allem online-affine Frauen aus Deutschland, Österreich und der Schweiz, aber sicher auch europaweit im Alter von 21-45.
> Aufgabenstellung.
Wir sind auf der Suche nach einem Konzept für unsere Produktverpackungen bzw. Etiketten. Bei den Pflegeprodukten verzichten wir bewusst auf eine Umverpackung.
Konkret geplant sind ein Rasierhobel, dafür haben wir eine schöne Umverpackung. Außerdem starten wir mit Rasieröl, Rasierseife und einem After Shave Balsam. Es werden später noch andere Artikel dazukommen, eine Deocreme zum Beispiel.
Rasieröl, Rasiercreme und After Shave Balsam duften nach Orangen, es werden zwei oder drei weitere Duftrichtungen folgen, die eine wird beispielsweise nach Beeren duften, die andere nach Pfirsich und Mango – bitte beachte das bei der Erstellung des Konzeptes, die Unterschiede sollten später auf den ersten Blick erkennbar sein.
Zurück zum Thema Orange: Wir würden den Duft als leicht herben Zitrusduft bezeichnen.
> Die Maße.
• Umverpackung Rasierhobel, weißer Karton (165x90x40mm)
• Rasieröl 30ml (Etikett: 100x46mm)
• Rasiercreme 60ml (Etikett: 156x32mm)
• After Shave Balsam 60ml (Etikett: 156x32mm)
> Zwingend erforderliche Angaben.
Da es sich um Kosmetikprodukte handelt, sind einige Angaben auf dem Label zwingend erforderlich, beispielhaft sollen die folgenden Infos als Platzhalter dienen.
• Hergestellt für Friedrich Lautner e.K. von greenpines, Lindenhofweg 7, 83109 Kolbermoor
• Ingredients: Aqua, Stearic Acid, Cocos Nucifera oil, Glycerin, Potassium Hydroxide, Litsea Cubeba oil, (and) Citrus Sinensis Peel oil, Orbignya Oleifera oil, Sodium Hydroxide, Macadamia ternifolia oil, Talc, Kaolin, Citric Acid, Simmondsia chinensis oil, Maris sal, C.I. 77892 (and) Rad Clay, Citral, Limonene, Linalool, Geraniol
• Platz für einen Barcode
• Rasieröl sind 30ml / 1.01 FL.OZ. ODER Creme & Balsam jeweils 60ml / 2.03 FL. OZ.
Wir haben ein Bild der aktuellen Gefäße beigefügt, es kann aber durchaus sein, dass wir uns noch umen..

```html
<!DOCTYPE html>
<html lang="de">
<head>
<meta charset="utf-8">
<title>Sanft – Rasieröl Etikett und Rasierhobel Verpackung</title>
<link href="https://fonts.googleapis.com/css2?family=Abril+Fatface&family=Special+Elite&family=Homemade+Apple&family=Nunito+Sans:wght@300;400;800&display=swap" rel="stylesheet">
<style>
  :root {
    --backdrop: #dcdcdc;
    --label-white: #f1f1f0;
    --carton: #ebe9e6;
    --sage: #87a69f;
    --sage-soft: #d3dbd8;
    --blossom: #b9a679;
    --navy: #1e2a4c;
    --orange: #e0791f;
    --ink: #2a2a2a;
    --ink-light: #8a8a8a;
  }
  * { margin: 0; padding: 0; box-sizing: border-box; }
  html, body { width: 1200px; height: 900px; overflow: hidden; }
  body {
    background: var(--backdrop);
    font-family: "Nunito Sans", sans-serif;
    position: relative;
  }

  /* Rasieröl label, laid flat */
  .oil-label {
    position: absolute;
    left: 240px; top: 230px;
    width: 300px; height: 420px;
    background: var(--label-white);
    overflow: hidden;
    box-shadow: 0 2px 6px rgba(0,0,0,.08);
  }
  .oil-label .brand-disc {
    position: absolute;
    left: 75px; top: 40px;
    width: 150px; height: 150px;
    border-radius: 50%;
    background: var(--sage);
    display: flex; align-items: center; justify-content: center;
  }
  .brand-name {
    font-family: "Nunito Sans", sans-serif;
    font-weight: 300;
    color: var(--label-white);
    letter-spacing: .04em;
  }
  .oil-label .brand-name { font-size: 40px; }
  .oil-label .scent-band {
    position: absolute; left: 0; bottom: 0;
    width: 100%; height: 190px;
  }
  .oil-label .band-text {
    position: absolute; left: 10px; bottom: 0;
    width: 210px; height: 170px;
    padding-top: 38px;
    text-align: center;
  }
  .product-title {
    font-family: "Abril Fatface", serif;
    font-size: 24px;
    color: var(--navy);
    line-height: 1;
  }
  .scent-name {
    font-family: "Special Elite", monospace;
    font-size: 20px;
    color: var(--orange);
    margin-top: 4px;
    white-space: nowrap;
  }
  .origin {
    font-family: "Homemade Apple", cursive;
    font-size: 10px;
    color: var(--navy);
    margin-top: 18px;
  }
  .volume {
    font-family: "Special Elite", monospace;
    font-size: 11px;
    color: var(--navy);
    margin-top: 4px;
  }
  .blossom-art {
    position: absolute; left: 226px; bottom: 28px;
    width: 62px; height: 110px;
    background: linear-gradient(180deg, rgba(185,166,121,.15), rgba(185,166,121,.4));
  }

  /* Rasierhobel carton, front panel */
  .razor-box {
    position: absolute;
    left: 640px; top: 150px;
    width: 330px; height: 605px;
    background: var(--carton);
    overflow: hidden;
    box-shadow: 0 2px 8px rgba(0,0,0,.08);
  }
  .razor-box .leaf-art {
    position: absolute; left: 70px; top: 220px;
    width: 210px; height: 300px;
    background: linear-gradient(180deg, rgba(211,219,216,.9), rgba(211,219,216,0));
  }
  .razor-box .brand-disc {
    position: absolute;
    left: 45px; top: 70px;
    width: 240px; height: 240px;
    border-radius: 50%;
    background: var(--sage);
    display: flex; align-items: center; justify-content: center;
  }
  .razor-box .brand-name { font-size: 62px; }
  .box-title {
    position: absolute; left: 45px; top: 380px;
    font-weight: 800;
    font-size: 26px;
    letter-spacing: .01em;
    color: var(--ink);
    line-height: 1.05;
  }
  .box-subtitle {
    position: absolute; left: 45px; top: 410px;
    font-weight: 300;
    font-size: 26px;
    color: var(--ink-light);
    line-height: 1.05;
  }
  .box-tagline {
    position: absolute; left: 45px; bottom: 60px;
    font-weight: 400;
    font-size: 12px;
    letter-spacing: .02em;
    color: var(--ink);
  }
</style>
</head>
<body>

  <section class="oil-label">
    <div class="brand-disc"><span class="brand-name">sanft</span></div>
    <svg class="scent-band" viewBox="0 0 300 190" preserveAspectRatio="none" aria-hidden="true">
      <path d="M0 22 C40 12 80 26 120 16 C160 6 210 20 250 10 C270 6 290 12 300 8 L300 190 L0 190 Z" fill="var(--sage)"/>
    </svg>
    <div class="blossom-art" role="img" aria-label="Feine Linienzeichnung einer Orangenblüte"></div>
    <div class="band-text">
      <p class="product-title">Rasieröl</p>
      <p class="scent-name">Orange Blossom</p>
      <p class="origin">handmade in germany</p>
      <p class="volume">30ml / 1.01 FL.OZ.</p>
    </div>
  </section>

  <section class="razor-box">
    <div class="leaf-art" role="img" aria-label="Großes, blasses Blatt als Hintergrundmotiv"></div>
    <div class="brand-disc"><span class="brand-name">sanft</span></div>
    <h1 class="box-title">RASIERHOBEL</h1>
    <p class="box-subtitle">EXTRA SANFT</p>
    <p class="box-tagline">RASIERER FÜR FRAUEN</p>
  </section>

</body>
</html>
```